Pitch Deck presentation

Design multiple graphics and slides that can be used in a PowerPoint presentation.
4 infographics, text templates and blank templates
Attached you will find the infographics references and a couple of styles we would like to have on the presentations
We prefer a simpler design with not too much background noise or colors(prefer to have whiter backgrounds)
The infographics in the whiteboard should be presented 1 per slide with space on the right side to write text for explanation.
4 total columns will be the equivalent to the 4 different slides with design in the presentation.
Attached you have our colors and logos.
https://files.plomvarek.net/share/7qKtr2WnZe4xBvLp9HsD3aYuM0cFgR?mode=view
You can reach out to me with any questions at my email mkestrubio@hallowpine.com

```html
<!DOCTYPE html>
<html lang="en">
<head>
<meta charset="utf-8">
<title>Ridgeline Haul — Pitch Deck Slides</title>
<link rel="stylesheet" href="https://fonts.googleapis.com/css2?family=Roboto:wght@300;400;700&family=Montserrat:wght@300;400;600&display=swap">
<style>
  :root {
    --orange: #e8501e;
    --ink: #333333;
    --dark: #1c1c1e;
    --slide-bg: #f2f2f2;
    --grey-text: #555555;
    --light-text: #777777;
    --table-dark: #3a3a3a;
    --faint: #e2e2e2;
    --white: #ffffff;
  }
  * { box-sizing: border-box; margin: 0; padding: 0; }
  html, body { width: 1018px; height: 1200px; overflow: hidden; background: var(--white); }
  body { position: relative; font-family: "Roboto", Arial, sans-serif; color: var(--ink); }

  .slide { position: absolute; width: 474px; height: 267px; background: var(--slide-bg); overflow: hidden; }
  .col-a { left: 28px; } .col-b { left: 518px; }
  .row-1 { top: 26px; } .row-2 { top: 313px; } .row-3 { top: 603px; } .row-4 { top: 893px; }

  .tab-top { position: absolute; top: 0; left: 26px; width: 35px; height: 3px; background: var(--orange); }
  .tab-bottom { position: absolute; bottom: 0; left: 432px; width: 35px; height: 3px; background: var(--orange); }
  .page-no { position: absolute; right: 14px; top: 248px; font-size: 7px; color: var(--ink); }

  .slide-title { position: absolute; left: 16px; top: 13px; font-size: 15px; font-weight: 400; color: var(--ink); }
  .slide-title .accent { color: var(--orange); }
  .brand-name { position: absolute; right: 14px; top: 11px; font-size: 19px; font-weight: 700; color: var(--ink); letter-spacing: 0.5px; }

  /* Cover */
  .cover { background: var(--dark); }
  .cover-photo { position: absolute; inset: 0; background: linear-gradient(160deg, #5a5a5c 0%, #2e2e30 45%, #141416 100%); }
  .cover-name { position: absolute; left: 0; right: 0; top: 62px; text-align: center; font-size: 56px; font-weight: 700; color: var(--white); letter-spacing: 2px; }
  .cover-tagline { position: absolute; left: 0; right: 0; top: 160px; text-align: center; font-size: 15px; font-weight: 400; color: var(--white); }
  .cover-line { position: absolute; left: 0; right: 0; top: 192px; text-align: center; font-size: 14px; color: var(--white); }
  .cover-line strong { color: var(--orange); font-weight: 700; }

  /* About */
  .about-mission { position: absolute; left: 16px; top: 56px; width: 262px; font-size: 10.5px; line-height: 15px; color: var(--ink); }
  .about-point { position: absolute; left: 16px; width: 262px; font-family: "Montserrat", Arial, sans-serif; font-size: 8px; font-weight: 300; line-height: 12px; color: var(--grey-text); }
  .about-point .label { font-family: "Roboto", Arial, sans-serif; font-size: 10.5px; font-weight: 400; color: var(--orange); }
  .about-photo { position: absolute; left: 285px; top: 54px; width: 181px; height: 187px; background: linear-gradient(180deg, #e55a26 0%, #d9421a 100%); }
  .photo-tab { position: absolute; height: 3px; width: 34px; background: var(--white); }

  /* Chart */
  .chart-card { position: absolute; left: 17px; top: 53px; width: 220px; height: 187px; background: var(--white); }
  .chart-copy { position: absolute; left: 257px; top: 56px; width: 207px; font-size: 7.6px; line-height: 12.4px; color: var(--ink); }

  /* Welcome */
  .welcome-lead { position: absolute; left: 17px; top: 56px; width: 444px; font-family: "Montserrat", Arial, sans-serif; font-size: 8.1px; font-weight: 600; line-height: 12.4px; color: var(--ink); }
  .welcome-body { position: absolute; left: 17px; top: 168px; width: 444px; font-family: "Montserrat", Arial, sans-serif; font-size: 8.1px; font-weight: 300; line-height: 12.4px; color: var(--grey-text); }

  /* Blank */
  .watermark-name { position: absolute; left: 0; right: 0; top: 92px; text-align: center; font-size: 56px; font-weight: 700; color: var(--faint); letter-spacing: 2px; }

  /* Value table */
  .value-table { position: absolute; left: 18px; top: 62px; width: 445px; border-collapse: collapse; table-layout: fixed; }
  .value-table th { height: 31px; background: var(--orange); color: var(--white); font-size: 8.5px; font-weight: 400; border-right: 1px solid #f0774d; }
  .value-table td { height: 32.5px; background: var(--table-dark); color: #d8d8d8; font-family: "Montserrat", Arial, sans-serif; font-size: 5.6px; font-weight: 400; line-height: 7.6px; text-align: center; border-right: 1px solid #555; border-top: 1px solid #555; padding: 0 6px; }

  /* Services */
  .services-graphic { position: absolute; left: 0; top: 0; width: 474px; height: 267px; }
  .service-name { position: absolute; left: 36px; top: 138px; width: 144px; text-align: center; font-size: 17px; font-weight: 700; color: var(--ink); }
  .service-item { position: absolute; width: 196px; font-size: 5.2px; line-height: 8.4px; color: var(--ink); }

  /* Thank you */
  .thanks { position: absolute; left: 0; right: 0; top: 56px; text-align: center; font-size: 46px; font-weight: 300; color: var(--ink); }
  .thanks-name { position: absolute; left: 0; right: 0; top: 133px; text-align: center; font-size: 56px; font-weight: 700; color: var(--ink); letter-spacing: 2px; }
</style>
</head>
<body>

  <!-- Cover -->
  <section class="slide cover col-a row-1">
    <div class="cover-photo" role="img" aria-label="Black and white photo of a semi truck on the road under a cloudy sky"></div>
    <div class="tab-top"></div>
    <div class="cover-name">RIDGELINE HAUL</div>
    <div class="cover-tagline">United for Independence</div>
    <div class="cover-line">Your Comprehensive <strong>Freight Management</strong> Solution</div>
    <div class="tab-bottom"></div>
  </section>

  <!-- About -->
  <section class="slide col-b row-1">
    <div class="tab-top"></div>
    <h2 class="slide-title">About Us</h2>
    <div class="brand-name">RIDGELINE HAUL</div>
    <p class="about-mission">Ridgeline Haul’s Mission is to reintroduce Freedom in the freight industry by providing a sustainable Free Market solution through moral Innovation.</p>
    <p class="about-point" style="top:114px"><span class="label">For Freedom:</span> We believe in challenging the system that limits our choices and find it our duty to pioneer the path to restore America to her rightful place where the quality of our success grows with each interaction.</p>
    <p class="about-point" style="top:180px"><span class="label">A Free Market Solution:</span> Freedom is created for the freight industry through a new system of stable voluntary exchanges where interactions are honest and transparent, creating ever expanding opportunities for both shippers and carriers.</p>
    <div class="about-photo" role="img" aria-label="Row of parked trucks tinted orange">
      <div class="photo-tab" style="top:0; right:12px;"></div>
      <div class="photo-tab" style="bottom:0; left:14px;"></div>
    </div>
    <div class="page-no">Page No:02</div>
    <div class="tab-bottom"></div>
  </section>

  <!-- Chart -->
  <section class="slide col-a row-2">
    <div class="tab-top"></div>
    <h2 class="slide-title">Charts <span class="accent">Table</span></h2>
    <div class="brand-name">RIDGELINE HAUL</div>
    <div class="chart-card">
      <svg width="220" height="187" viewBox="0 0 220 187" font-family="Roboto, Arial, sans-serif" font-size="8" fill="#333">
        <line x1="24" y1="14" x2="24" y2="164" stroke="#e6e6e6" stroke-width="0.6"/>
        <line x1="6" y1="164" x2="210" y2="164" stroke="#e6e6e6" stroke-width="0.6"/>
        <text x="8" y="17">50</text><text x="8" y="53">40</text><text x="8" y="88">30</text>
        <text x="8" y="124">20</text><text x="8" y="159">10</text>
        <text x="36" y="181">100</text><text x="74" y="181">200</text><text x="112" y="181">300</text>
        <text x="150" y="181">400</text><text x="188" y="181">500</text>
        <polyline points="42,142 80,120 118,83 158,115 195,43" fill="none" stroke="#999" stroke-width="0.6"/>
        <g fill="#f6c9b8"><circle cx="42" cy="142" r="4"/><circle cx="80" cy="120" r="4"/><circle cx="118" cy="83" r="4"/><circle cx="158" cy="115" r="4"/><circle cx="195" cy="43" r="4"/></g>
        <g fill="#e8501e"><circle cx="42" cy="142" r="1.8"/><circle cx="80" cy="120" r="1.8"/><circle cx="118" cy="83" r="1.8"/><circle cx="158" cy="115" r="1.8"/><circle cx="195" cy="43" r="1.8"/></g>
      </svg>
    </div>
    <p class="chart-copy">Sed ut perspiciatis unde omnis iste natus error sit voluptatem accusantium doloremque laudantium, totam rem aperiam, eaque ipsa quae ab illo inventore veritatis et quasi architecto beatae vitae dicta sunt explicabo. Nemo enim ipsam voluptatem quia voluptas sit aspernatur aut odit aut fugit, sed quia consequuntur magni dolores eos qui ratione voluptatem sequi nesciunt. Neque porro quisquam est, qui dolorem ipsum quia dolor sit amet, consectetur, adipisci velit, sed quia non numquam eius modi tempora incidunt ut labore et dolore magnam aliquam quaerat voluptatem. Neque porro quisquam est, qui dolorem ipsum quia dolor sit amet, consectetur, adipisci velit, sed quia non numquam eius modi tempora incidunt ut labore et dolore magnam aliquam quaerat voluptatem.</p>
    <div class="page-no">Page No:03</div>
    <div class="tab-bottom"></div>
  </section>

  <!-- Welcome -->
  <section class="slide col-b row-2">
    <div class="tab-top"></div>
    <h2 class="slide-title">Welcome <span class="accent">To</span></h2>
    <div class="brand-name">RIDGELINE HAUL</div>
    <p class="welcome-lead">Sed ut perspiciatis unde omnis iste natus error sit voluptatem accusantium doloremque laudantium, totam rem aperiam, eaque ipsa quae ab illo inventore veritatis et quasi architecto beatae vitae dicta sunt explicabo. Nemo enim ipsam voluptatem quia voluptas sit aspernatur aut odit aut fugit, sed quia consequuntur magni dolores eos qui ratione voluptatem sequi nesciunt. Neque porro quisquam est, qui dolorem ipsum quia dolor sit amet, consectetur, adipisci velit, sed quia non numquam eius modi tempora incidunt ut labore et dolore magnam aliquam quaerat voluptatem. Neque porro quisquam est, qui dolorem ipsum quia dolor sit amet, consectetur, adipisci velit, sed quia non numquam eius modi tempora incidunt ut labore et dolore magnam aliquam quaerat voluptatem.</p>
    <p class="welcome-body">Sed ut perspiciatis unde omnis iste natus error sit voluptatem accusantium doloremque laudantium, totam rem a ne voluptatem sequi nesciunt. Neque porro quisquam est, qui dolorem ipsum quia dolor sit amet, consectetur, adipisci velit, sed quia non numquam eius modi tempora incidunt ut labore et dolore magnam aliquam quaerat voluptatem. Neque porro quisquam est, qui dolorem ipsum quia dolor sit amet, consectetur, adipisci velit, sed quia non numquam eius modi tempora incidunt ut labore et dolore magnam aliquam quaerat voluptatem.</p>
    <div class="page-no">Page No:04</div>
    <div class="tab-bottom"></div>
  </section>

  <!-- Blank template -->
  <section class="slide col-a row-3">
    <div class="tab-top"></div>
    <div class="brand-name">RIDGELINE HAUL</div>
    <div class="watermark-name">RIDGELINE HAUL</div>
    <div class="page-no">Page No:05</div>
    <div class="tab-bottom"></div>
  </section>

  <!-- Value table -->
  <section class="slide col-b row-3">
    <div class="tab-top"></div>
    <h2 class="slide-title">Our <span class="accent">Value</span></h2>
    <div class="brand-name">RIDGELINE HAUL</div>
    <table class="value-table">
      <thead><tr><th>Nemo enim ipsam</th><th>Nemo enim ipsam</th><th>Nemo enim ipsam</th><th>Nemo enim ipsam</th></tr></thead>
      <tbody>
        <tr><td>Neque porro quisquam est, qui dolorem ipsum quia</td><td>Neque porro quisquam est, qui dolorem ipsum quia</td><td>Neque porro quisquam est, qui dolorem ipsum quia</td><td>Neque porro quisquam est, qui dolorem ipsum quia</td></tr>
        <tr><td>Neque porro quisquam est, qui dolorem ipsum quia</td><td>Neque porro quisquam est, qui dolorem ipsum quia</td><td>Neque porro quisquam est, qui dolorem ipsum quia</td><td>Neque porro quisquam est, qui dolorem ipsum quia</td></tr>
        <tr><td>Neque porro quisquam est, qui dolorem ipsum quia</td><td>Neque porro quisquam est, qui dolorem ipsum quia</td><td>Neque porro quisquam est, qui dolorem ipsum quia</td><td>Neque porro quisquam est, qui dolorem ipsum quia</td></tr>
        <tr><td>Neque porro quisquam est, qui dolorem ipsum quia</td><td>Neque porro quisquam est, qui dolorem ipsum quia</td><td>Neque porro quisquam est, qui dolorem ipsum quia</td><td>Neque porro quisquam est, qui dolorem ipsum quia</td></tr>
      </tbody>
    </table>
    <div class="page-no">Page No:06</div>
    <div class="tab-bottom"></div>
  </section>

  <!-- Services -->
  <section class="slide col-a row-4">
    <div class="tab-top"></div>
    <h2 class="slide-title">Our <span class="accent">Services</span></h2>
    <div class="brand-name">RIDGELINE HAUL</div>
    <svg class="services-graphic" viewBox="0 0 474 267">
      <path d="M108 63 A86 86 0 0 1 108 235" fill="none" stroke="#e8501e" stroke-width="16"/>
      <circle cx="108" cy="149" r="72" fill="#ffffff"/>
      <g fill="none" stroke="#aaa" stroke-width="0.6" stroke-dasharray="2 1.5">
        <polyline points="166,84 184,71 216,71"/>
        <polyline points="186,112 198,103 233,103"/>
        <polyline points="196,148 244,148"/>
        <polyline points="186,184 198,191 233,191"/>
        <polyline points="166,212 182,223 214,223"/>
      </g>
      <g fill="#e8501e">
        <circle cx="222" cy="71" r="5"/><circle cx="239" cy="103" r="5"/><circle cx="250" cy="148" r="5"/>
        <circle cx="239" cy="191" r="5"/><circle cx="220" cy="223" r="5"/>
      </g>
    </svg>
    <div class="service-name">RIDGELINE HAUL</div>
    <p class="service-item" style="left:240px; top:54px;">Sed ut perspiciatis unde omnis iste natus error sit voluptatem accusantium doloremque laudantium, totam rem aperiam, eaque ipsa quae ab illo inventore veritatis et quasi architecto beatae vitae dicta sunt explicabo.</p>
    <p class="service-item" style="left:250px; top:90px;">Sed ut perspiciatis unde omnis iste natus error sit voluptatem accusantium doloremque laudantium, totam rem aperiam, eaque ipsa quae ab illo inventore veritatis et quasi architecto beatae vitae dicta sunt explicabo.</p>
    <p class="service-item" style="left:265px; top:134px;">Sed ut perspiciatis unde omnis iste natus error sit voluptatem accusantium doloremque laudantium, totam rem aperiam, eaque ipsa quae ab illo inventore veritatis et quasi architecto beatae vitae dicta sunt explicabo.</p>
    <p class="service-item" style="left:250px; top:178px;">Sed ut perspiciatis unde omnis iste natus error sit voluptatem accusantium doloremque laudantium, totam rem aperiam, eaque ipsa quae ab illo inventore veritatis et quasi architecto beatae vitae dicta sunt explicabo.</p>
    <p class="service-item" style="left:240px; top:215px;">Sed ut perspiciatis unde omnis iste natus error sit voluptatem accusantium doloremque laudantium, totam rem aperiam, eaque ipsa quae ab illo inventore veritatis et quasi architecto beatae vitae dicta sunt explicabo.</p>
    <div class="page-no">Page No:07</div>
    <div class="tab-bottom"></div>
  </section>

  <!-- Thank you -->
  <section class="slide col-b row-4">
    <div class="tab-top"></div>
    <div class="thanks">THANK YOU</div>
    <div class="thanks-name">RIDGELINE HAUL</div>
    <div class="tab-bottom" style="left:415px;"></div>
  </section>

</body>
</html>
```